Business Card for Industrial Distributor

We need a business card design for an industrial distributor. We sell machine parts for the manufacturing and oil industry. We would like the cards to look clean and modern but with a touch of industry.

Our colors are blue/white.

Please feel free to visit our website www.korvelpartsco.com

Target Market(s)

mexican manufacturers in the automobile/aerospace industry

Industry/Entity Type

Industrial

Colors
ffffff
0555a3

```html
<!DOCTYPE html>
<html lang="en">
<head>
<meta charset="utf-8">
<title>Korvel Business Card</title>
<link href="https://fonts.googleapis.com/css2?family=Exo+2:wght@500;700&family=Lato:wght@400;700&display=swap" rel="stylesheet">
<style>
  :root {
    --stage: #3c3c3c;
    --brand-blue: #0555a3;
    --blue-light: #2670b3;
    --blue-deep: #2a56a0;
    --navy: #26308f;
    --white: #ffffff;
    --grey-text: #8a8a8a;
  }
  * { margin: 0; padding: 0; box-sizing: border-box; }
  html, body { width: 1200px; height: 810px; overflow: hidden; }
  body {
    background: var(--stage);
    font-family: "Lato", sans-serif;
    position: relative;
  }
  .card {
    position: absolute;
    top: 250px;
    width: 540px;
    height: 309px;
    box-shadow: 0 6px 18px rgba(0,0,0,0.35);
  }
  /* Back side */
  .card-back {
    left: 40px;
    background: radial-gradient(ellipse at 50% 40%, var(--blue-light) 0%, var(--brand-blue) 55%, var(--blue-deep) 100%);
    color: var(--white);
  }
  .back-mark {
    position: absolute;
    left: 0; right: 0; top: 92px;
    display: flex; align-items: center; justify-content: center; gap: 14px;
  }
  .back-mark .dot {
    width: 46px; height: 46px; border-radius: 50%; background: var(--white);
  }
  .back-mark .name {
    font-family: "Exo 2", sans-serif; font-weight: 700; font-size: 44px; color: var(--white);
  }
  .back-url {
    position: absolute; left: 0; right: 0; bottom: 40px;
    text-align: center; font-size: 13px; letter-spacing: 0.3px;
  }
  /* Front side */
  .card-front {
    left: 620px;
    background: var(--white);
  }
  .front-logo {
    position: absolute; left: 34px; top: 40px;
    display: flex; align-items: center; gap: 12px;
  }
  .front-logo .dot {
    width: 44px; height: 44px; border-radius: 50%; background: var(--brand-blue);
  }
  .front-logo .name {
    font-family: "Exo 2", sans-serif; font-weight: 700; font-size: 46px; color: var(--navy);
  }
  .person {
    position: absolute; right: 34px; top: 46px; text-align: right;
  }
  .person-name {
    font-family: "Exo 2", sans-serif; font-weight: 500; font-size: 22px; color: var(--navy); line-height: 1.1;
  }
  .person-title {
    font-family: "Exo 2", sans-serif; font-size: 13px; color: var(--grey-text);
  }
  .company {
    position: absolute; right: 34px; top: 140px; text-align: right; line-height: 1.35;
  }
  .company-name { font-weight: 700; font-size: 13px; color: var(--navy); }
  .company-line { font-size: 13px; color: var(--grey-text); }
  .contacts {
    position: absolute; left: 34px; bottom: 30px; list-style: none;
    font-size: 14px; color: var(--grey-text); line-height: 1.35;
  }
  .contacts li { display: flex; align-items: center; gap: 7px; }
  .contacts svg { width: 13px; height: 13px; fill: var(--navy); flex: none; }
</style>
</head>
<body>
  <section class="card card-back">
    <div class="back-mark">
      <span class="dot"></span>
      <span class="name">Korvel</span>
    </div>
    <p class="back-url">www.korvelpartsco.com</p>
  </section>

  <section class="card card-front">
    <div class="front-logo">
      <span class="dot"></span>
      <span class="name">Korvel</span>
    </div>

    <div class="person">
      <p class="person-name">Daniel Reyes</p>
      <p class="person-title">President &amp; CEO</p>
    </div>

    <div class="company">
      <p class="company-name">korvel international Corp.</p>
      <p class="company-line">4180 Harbor Mill Rd,</p>
      <p class="company-line">Laredo, TX 78041</p>
    </div>

    <ul class="contacts">
      <li>
        <svg viewBox="0 0 16 16" aria-hidden="true"><path d="M1 5c0-2 3-3 7-3s7 1 7 3v1h-4V5H5v1H1z M4 7h8l2 7H2z"/></svg>
        (956) 555 - 0142
      </li>
      <li>
        <svg viewBox="0 0 16 16" aria-hidden="true"><path d="M4 1h8v4H4z M1 6h14v6h-3v3H4v-3H1z M5 10v4h6v-4z"/></svg>
        (956) 555 - 0147
      </li>
      <li>
        <svg viewBox="0 0 16 16" aria-hidden="true"><path d="M1 3h14v10H1z M2 4l6 5 6-5" fill="none" stroke="#26308f" stroke-width="1.6"/></svg>
        sales@korvelpartsco.com
      </li>
      <li>
        <svg viewBox="0 0 16 16" aria-hidden="true"><g fill="none" stroke="#26308f" stroke-width="1.4"><circle cx="8" cy="8" r="6.5"/><ellipse cx="8" cy="8" rx="3" ry="6.5"/><path d="M1.5 8h13M2.5 5h11M2.5 11h11"/></g></svg>
        www.korvelpartsco.com
      </li>
    </ul>
  </section>
</body>
</html>
```